QuillVane needs a dashboard page designed

Redesign the dashboard shown in the provided images.

There are two images:
- dashboard.png
- dashboard-expanded.png

NOTE: The vocabulary navigation on the left will be a very long list of words 100s, so keep that in mind when you're designing both the vocab navigation and the expanded vocab popup.

In the dashboard.png picture, there needs to be a progress chart showing the word progress like the following: review 1(show it as completed) -> review 2(show the user they are here) -> review 3(unvisited) -> review 4(unvisited)

The do-not-design-this-page.png image is for your reference only. It is not to be designed. Use it to understand the overall look and feel of the website to help you create the best dashboard page possible.
Updates

Need extra days to review

Industry/Entity Type

Education English learning

Number of Pages Required

1 page

Requirements
Must have
• The main navigation and main header cannot change between pages. See the do-not-design page for the main navigateion and header.
Should not have
• Do not add a person profile. We will not have images of our users. Keep the icons in the main navigation as they are.

```html
<!DOCTYPE html>
<html lang="en">
<head>
<meta charset="utf-8">
<title>QuillVane Dashboard</title>
<link href="https://fonts.googleapis.com/css2?family=Lato:wght@400;700&display=swap" rel="stylesheet">
<style>
:root{
  --side:#2d333b;
  --side-band:#8b9097;
  --topbar:#9a9da2;
  --blue:#1a73e8;
  --text:#222;
  --muted:#555a60;
  --pale:#e3e4e6;
  --pale-text:#b4b7bb;
  --red:#e02424;
  --green:#19c24a;
  --star:#f6b91d;
  --close:#d63b3b;
  --footer:#eeeeef;
}
*{box-sizing:border-box;margin:0;padding:0}
html,body{width:799px;height:1200px;overflow:hidden;background:#fff}
body{font-family:'Lato',sans-serif;color:var(--text)}
.board{width:1568px;height:2355px;transform:scale(0.50957);transform-origin:0 0;position:relative}
.screen{position:absolute;left:33px;width:1502px;height:1126px;background:#fff;overflow:hidden}
.screen.first{top:32px}
.screen.second{top:1196px}
.abs{position:absolute}
/* sidebar */
.sidebar{position:absolute;left:0;top:0;width:333px;height:1126px;background:var(--side);border-bottom-right-radius:22px;color:#fff;z-index:2}
.brand{position:absolute;left:0;top:38px;width:306px;text-align:center;font-family:'Lato',sans-serif;font-weight:700;font-size:32px;color:#fff}
.brand-rule{position:absolute;left:0;top:103px;width:333px;height:2px;background:#e8e8e8}
.expand{position:absolute;left:30px;top:121px;font-size:17px;font-weight:700;display:flex;align-items:center;gap:10px}
.filter-bar{position:absolute;left:0;top:165px;width:333px;height:42px;background:var(--side-band);font-size:14px;padding:12px 28px}
.filter-bar svg{position:absolute;right:14px;top:16px}
.band{position:absolute;left:0;width:333px;height:48px;background:var(--side-band);display:flex;align-items:center;font-size:17px;font-weight:700}
.band .ico{position:absolute;left:24px;top:11px}
.band .label{position:absolute;top:13px}
.band .help{position:absolute;right:20px;top:13px}
.word{position:absolute;font-size:13px;color:#fff}
/* top bar */
.topbar{position:absolute;left:333px;top:0;width:1169px;height:72px;background:var(--topbar)}
.tab{position:absolute;top:13px;height:44px;border-radius:3px;background:#fff;font-size:15px;display:flex;align-items:center;gap:10px;padding-left:16px;color:#222;white-space:nowrap}
.tab.active{background:var(--blue);color:#fff}
.userbox{position:absolute;color:#fff;font-size:14px}
.avatar{position:absolute;left:1364px;top:16px;width:36px;height:36px;border-radius:50%;background:linear-gradient(135deg,#6b5a4d,#3a322d)}
/* review progress */
.step{position:absolute;top:105px;height:37px;font-size:13px;display:flex;align-items:center;padding-left:13px;gap:12px;border-radius:2px}
.step.done{background:#fff;border:1px solid #e4e4e4}
.step.current{background:var(--blue);color:#fff;font-weight:700}
.step.todo{background:var(--pale);color:var(--pale-text);justify-content:center;padding-left:0}
.bar-done{width:128px;height:3px;background:var(--red)}
.bar-now{width:128px;height:3px;background:linear-gradient(90deg,var(--green) 0 64%,#fff 64%)}
/* word header */
.word-title{position:absolute;left:397px;top:208px;font-size:21px;display:flex;align-items:center;gap:10px}
.cta{position:absolute;left:564px;top:206px;width:298px;height:45px;border-radius:4px;background:#8e9297;color:#fff;font-size:15px;font-weight:700;display:flex;align-items:center;gap:10px;padding-left:8px;box-shadow:0 2px 4px rgba(0,0,0,.2);white-space:nowrap}
.copy{position:absolute;font-size:14px;line-height:26.5px;color:var(--muted);white-space:nowrap}
.chart-card{position:absolute;left:398px;top:429px;width:1076px;height:505px;background:#fff;box-shadow:0 0 8px rgba(0,0,0,.1)}
.analysis-title{position:absolute;left:400px;top:965px;font-size:19px;font-weight:700;color:#111}
.footer{position:absolute;left:333px;top:1104px;width:1169px;height:22px;background:var(--footer);font-size:11px;text-align:right;padding:4px 32px 0 0;color:#222}
/* modal state */
.dim{position:absolute;inset:0;background:rgba(18,20,24,.55);z-index:5}
.filter-bar.lifted{z-index:6}
.pointer{position:absolute;left:333px;top:177px;width:0;height:0;border-top:10px solid transparent;border-bottom:10px solid transparent;border-left:20px solid var(--side-band);z-index:6}
.modal{position:absolute;left:359px;top:164px;width:1073px;height:395px;background:#fff;border-radius:16px;z-index:7}
.modal .select{position:absolute;left:45px;top:36px;width:131px;height:34px;border:1.5px solid #3d7be0;border-radius:3px;font-size:11px;padding:9px 0 0 18px}
.modal .select svg{position:absolute;right:14px;top:13px}
.modal .close{position:absolute;left:1019px;top:26px}
.mhead{position:absolute;left:95px;font-size:15px;color:#444}
.mword{position:absolute;font-size:13px;color:#9a9da1;white-space:nowrap}
.mword.current{color:var(--close);font-weight:700;font-size:12px}
.mico{position:absolute;left:48px}
</style>
</head>
<body>
<div class="board">

<!-- ===== Dashboard ===== -->
<section class="screen first">
  <aside class="sidebar">
    <div class="brand">QuillVane</div>
    <div class="brand-rule"></div>
    <div class="expand">Expand
      <svg width="18" height="18" viewBox="0 0 18 18" fill="none" stroke="#fff" stroke-width="1.6"><path d="M7 3H2v13h13v-5"/><path d="M10 2h6v6M16 2 8 10"/></svg></div>
    <div class="filter-bar">All<svg width="18" height="10" viewBox="0 0 18 10"><path d="M0 0h18L9 10z" fill="#fff"/></svg></div>

    <div class="band" style="top:230px">
      <svg class="ico" width="28" height="28" viewBox="0 0 28 28" fill="none" stroke="#fff" stroke-width="1.6"><path d="M24 14A10 10 0 1 1 14 4"/><path d="M18 5l2 1.2M22 8l1 2" stroke-dasharray="2 2"/><path d="M14 8v6l-3 3"/></svg>
      <span class="label" style="left:67px">Short - Term Memory</span>
      <svg class="help" width="22" height="22" viewBox="0 0 22 22" fill="none" stroke="#fff" stroke-width="1.2"><circle cx="11" cy="11" r="10"/><text x="11" y="15.5" fill="#fff" stroke="none" font-size="12" text-anchor="middle" font-family="Lato">?</text></svg>
    </div>
    <span class="word" style="left:68px;top:290px">Grab</span>

    <div class="band" style="top:328px">
      <svg class="ico" width="30" height="30" viewBox="0 0 30 30" fill="none" stroke="#fff" stroke-width="1.6"><circle cx="15" cy="15" r="12"/><circle cx="15" cy="15" r="6" fill="#fff"/><circle cx="15" cy="15" r="2.5" fill="var(--side-band)" stroke="none"/></svg>
      <span class="label" style="left:63px">Working Memory</span>
      <svg class="help" width="22" height="22" viewBox="0 0 22 22" fill="none" stroke="#fff" stroke-width="1.2"><circle cx="11" cy="11" r="10"/><text x="11" y="15.5" fill="#fff" stroke="none" font-size="12" text-anchor="middle" font-family="Lato">?</text></svg>
    </div>
    <span class="word" style="left:73px;top:384px">Cool Down</span>
    <span class="word" style="left:73px;top:409px">Crave</span>
    <span class="word" style="left:73px;top:434px">Go For</span>
    <span class="word" style="left:73px;top:459px">Go- To</span>
    <span class="word" style="left:73px;top:484px">In The Mood For</span>
    <span class="word" style="left:73px;top:509px">Sip</span>
    <span class="word" style="left:73px;top:534px">Soothing</span>
    <span class="word" style="left:73px;top:559px">Stick With</span>
    <span class="word" style="left:73px;top:584px">Throw In/Throw On</span>

    <div class="band" style="top:633px">
      <svg class="ico" width="22" height="26" viewBox="0 0 22 26"><path d="M5 11V7a6 6 0 0 1 12 0v4" fill="none" stroke="#fff" stroke-width="2.4"/><rect x="2" y="11" width="18" height="14" rx="2" fill="#fff"/></svg>
      <span class="label" style="left:58px">Long-Term Memory</span>
      <svg class="help" width="22" height="22" viewBox="0 0 22 22" fill="none" stroke="#fff" stroke-width="1.2"><circle cx="11" cy="11" r="10"/><text x="11" y="15.5" fill="#fff" stroke="none" font-size="12" text-anchor="middle" font-family="Lato">?</text></svg>
    </div>
    <span class="word" style="left:67px;top:696px">Give It A Try</span>
  </aside>

  <header class="topbar"></header>
  <div class="tab active" style="left:391px;width:170px">
    <svg width="22" height="20" viewBox="0 0 22 20"><path d="M11 1 1 10h3v9h5v-6h4v6h5v-9h3z" fill="#fff"/></svg>Wordwell Tutor</div>
  <div class="tab" style="left:571px;width:138px">
    <svg width="22" height="18" viewBox="0 0 22 18" fill="none" stroke="#555" stroke-width="1.4"><rect x="1" y="3" width="20" height="14"/><path d="M4 6h5M4 9h5M4 12h5"/><text x="15" y="13" font-size="6" fill="#555" stroke="none" text-anchor="middle" font-family="Lato" font-weight="700">EN</text></svg>Daily English</div>
  <div class="tab" style="left:717px;width:122px;padding-left:20px;gap:14px">
    <svg width="18" height="15" viewBox="0 0 18 15"><path d="M6 3V1h6v2" fill="none" stroke="#666" stroke-width="1.5"/><rect x="0" y="3" width="18" height="12" rx="1.5" fill="#666"/><path d="M0 8h18" stroke="#fff"/></svg>Business</div>
  <svg class="abs" style="left:1282px;top:20px" width="28" height="28" viewBox="0 0 28 28" fill="none" stroke="#fff" stroke-width="1.8"><circle cx="14" cy="14" r="4.5"/><path d="M14 2v4M14 22v4M2 14h4M22 14h4M5.5 5.5l2.8 2.8M19.7 19.7l2.8 2.8M5.5 22.5l2.8-2.8M19.7 8.3l2.8-2.8"/><circle cx="14" cy="14" r="8.5"/></svg>
  <svg class="abs" style="left:1326px;top:23px" width="20" height="24" viewBox="0 0 20 24"><path d="M10 1 1 5v6c0 6 4 10 9 12 5-2 9-6 9-12V5z" fill="#fff"/><path d="M5 12l4 4 6-7" fill="none" stroke="#9a9da2" stroke-width="2"/></svg>
  <div class="avatar" role="img" aria-label="User avatar photo"></div>
  <div class="userbox" style="left:1408px;top:24px">Owen</div>
  <svg class="abs" style="left:1450px;top:27px" width="16" height="10" viewBox="0 0 16 10" fill="none" stroke="#fff" stroke-width="2"><path d="M1 1l7 7 7-7"/></svg>

  <div class="step done" style="left:392px;width:216px">Review 1<span class="bar-done"></span></div>
  <div class="step current" style="left:624px;width:215px">Review 2<span class="bar-now"></span></div>
  <div class="step todo" style="left:853px;width:98px">Review 3</div>
  <div class="step todo" style="left:969px;width:98px">Review 4</div>

  <div class="word-title">Grab
    <svg width="26" height="25" viewBox="0 0 26 25"><path d="M13 0l3.8 8.3 9.2 1-6.9 6.2 2 9L13 19.8 4.9 24.5l2-9L0 9.3l9.2-1z" fill="var(--star)"/></svg></div>
  <div class="cta"><svg width="20" height="20" viewBox="0 0 20 20" fill="none" stroke="#fff" stroke-width="1.5"><circle cx="10" cy="10" r="9"/><path d="M8 6l5 4-5 4z" fill="#fff"/></svg>Start Vocabulary Review Excercise 3</div>

  <p class="copy" style="left:397px;top:290px">The word "grab" is most commonly used as a verb, meaning to take something quickly or suddenly. Imagine you're running late for school. You don't have time for<br>breakfast, so you quickly grab an apple from the kitchen and rush out the door. As you reach the bus stop, your friend waves and says, "Hey! Let's grab a coffee after class."<br>Later, when you sit down, your phone starts ringing. You grab it from your bag and answer.</p>

  <div class="chart-card">
    <svg width="1076" height="505" viewBox="0 0 1076 505" font-family="Lato, sans-serif">
      <text x="538" y="77" font-size="23" fill="var(--blue)" text-anchor="middle">Learning Curve Graph</text>
      <g font-size="13" fill="#222">
        <text x="16" y="152">Long-Term Memory</text>
        <text x="16" y="257">Working Memory</text>
        <text x="16" y="328">Short - Term  Memory</text>
        <text x="16" y="372">Forgotten Memory</text>
      </g>
      <rect x="163" y="290" width="61" height="21" fill="#e3e4e6"/><text x="193" y="305" font-size="12" text-anchor="middle">May 18</text>
      <rect x="253" y="122" width="61" height="21" fill="#e3e4e6"/><text x="283" y="137" font-size="12" text-anchor="middle">May 19</text>
      <rect x="180" y="321" width="27" height="89" fill="var(--blue)"/>
      <rect x="321" y="128" width="27" height="282" fill="var(--blue)"/>
      <path d="M207 323C255 328 285 350 319 410" fill="none" stroke="#666" stroke-width="1.4" stroke-dasharray="1.5 3"/>
      <path d="M350 132C460 170 560 210 606 410" fill="none" stroke="#555" stroke-width="2.4" stroke-dasharray="2 6"/>
      <line x1="61" y1="410" x2="1063" y2="410" stroke="#b8babd" stroke-width="2"/>
      <g stroke="#b8babd" stroke-width="1.2">
        <path d="M83 412v15M149 412v15M224 412v15M289 412v15M349 412v15M414 412v15M481 412v15M547 412v15M606 412v15M672 412v15M731 412v15M796 412v15M855 412v15M921 412v15M982 412v15M1048 412v15"/>
      </g>
      <g font-size="13" fill="#555" text-anchor="middle">
        <text x="83" y="445">18 May</text><text x="149" y="445">12.00</text><text x="224" y="445">19 May</text><text x="289" y="445">12.00</text><text x="349" y="445">20 May</text><text x="414" y="445">12.00</text><text x="481" y="445">21 May</text><text x="547" y="445">12.00</text><text x="606" y="445">22 May</text><text x="672" y="445">12.00</text><text x="731" y="445">23 May</text><text x="796" y="445">12.00</text><text x="855" y="445">24 May</text><text x="921" y="445">12.00</text><text x="982" y="445">25 May</text><text x="1048" y="445">12.00</text>
      </g>
      <text x="538" y="475" font-size="14" fill="#222" text-anchor="middle">Data Range</text>
    </svg>
  </div>

  <h2 class="analysis-title">Wordwell Tutor Learning Analysis</h2>
  <p class="copy" style="left:398px;top:1003px">Lorem ipsum dolor sit amet, consectetur adipiscing elit, sed do eiusmod tempor incididunt ut labore et dolore magna aliqua. Ut enim ad minim veniam, quis nostrud<br>exercitation ullamco laboris nisi ut aliquip ex ea commodo consequat. Duis aute irure dolor in reprehenderit in voluptate velit esse cillum dolore eu fugiat nulla pariatur.<br>Excepteur sint occaecat cupidatat non proident, sunt in culpa qui officia deserunt mollit anim id est laborum.</p>
  <footer class="footer">Copyright © 2025  QuillVane</footer>
</section>

<!-- ===== Dashboard with vocabulary popup ===== -->
<section class="screen second">
  <aside class="sidebar">
    <div class="brand">QuillVane</div>
    <div class="brand-rule"></div>
    <div class="expand">Expand
      <svg width="18" height="18" viewBox="0 0 18 18" fill="none" stroke="#fff" stroke-width="1.6"><path d="M7 3H2v13h13v-5"/><path d="M10 2h6v6M16 2 8 10"/></svg></div>
    <div class="band" style="top:230px">
      <svg class="ico" width="28" height="28" viewBox="0 0 28 28" fill="none" stroke="#fff" stroke-width="1.6"><path d="M24 14A10 10 0 1 1 14 4"/><path d="M18 5l2 1.2M22 8l1 2" stroke-dasharray="2 2"/><path d="M14 8v6l-3 3"/></svg>
      <span class="label" style="left:67px">Short - Term Memory</span>
      <svg class="help" width="22" height="22" viewBox="0 0 22 22" fill="none" stroke="#fff" stroke-width="1.2"><circle cx="11" cy="11" r="10"/><text x="11" y="15.5" fill="#fff" stroke="none" font-size="12" text-anchor="middle" font-family="Lato">?</text></svg>
    </div>
    <span class="word" style="left:68px;top:290px">Grab</span>
    <div class="band" style="top:328px">
      <svg class="ico" width="30" height="30" viewBox="0 0 30 30" fill="none" stroke="#fff" stroke-width="1.6"><circle cx="15" cy="15" r="12"/><circle cx="15" cy="15" r="6" fill="#fff"/><circle cx="15" cy="15" r="2.5" fill="var(--side-band)" stroke="none"/></svg>
      <span class="label" style="left:63px">Working Memory</span>
      <svg class="help" width="22" height="22" viewBox="0 0 22 22" fill="none" stroke="#fff" stroke-width="1.2"><circle cx="11" cy="11" r="10"/><text x="11" y="15.5" fill="#fff" stroke="none" font-size="12" text-anchor="middle" font-family="Lato">?</text></svg>
    </div>
    <span class="word" style="left:73px;top:384px">Cool Down</span>
    <span class="word" style="left:73px;top:409px">Crave</span>
    <span class="word" style="left:73px;top:434px">Go For</span>
    <span class="word" style="left:73px;top:459px">Go- To</span>
    <span class="word" style="left:73px;top:484px">In The Mood For</span>
    <span class="word" style="left:73px;top:509px">Sip</span>
    <span class="word" style="left:73px;top:534px">Soothing</span>
    <span class="word" style="left:73px;top:559px">Stick With</span>
    <span class="word" style="left:73px;top:584px">Throw In/Throw On</span>
    <div class="band" style="top:633px">
      <svg class="ico" width="22" height="26" viewBox="0 0 22 26"><path d="M5 11V7a6 6 0 0 1 12 0v4" fill="none" stroke="#fff" stroke-width="2.4"/><rect x="2" y="11" width="18" height="14" rx="2" fill="#fff"/></svg>
      <span class="label" style="left:58px">Long-Term Memory</span>
      <svg class="help" width="22" height="22" viewBox="0 0 22 22" fill="none" stroke="#fff" stroke-width="1.2"><circle cx="11" cy="11" r="10"/><text x="11" y="15.5" fill="#fff" stroke="none" font-size="12" text-anchor="middle" font-family="Lato">?</text></svg>
    </div>
    <span class="word" style="left:67px;top:696px">Give It A Try</span>
  </aside>

  <header class="topbar"></header>
  <div class="tab active" style="left:391px;width:170px">
    <svg width="22" height="20" viewBox="0 0 22 20"><path d="M11 1 1 10h3v9h5v-6h4v6h5v-9h3z" fill="#fff"/></svg>Wordwell Tutor</div>
  <div class="tab" style="left:571px;width:138px">
    <svg width="22" height="18" viewBox="0 0 22 18" fill="none" stroke="#555" stroke-width="1.4"><rect x="1" y="3" width="20" height="14"/><path d="M4 6h5M4 9h5M4 12h5"/><text x="15" y="13" font-size="6" fill="#555" stroke="none" text-anchor="middle" font-family="Lato" font-weight="700">EN</text></svg>Daily English</div>
  <div class="tab" style="left:717px;width:122px;padding-left:20px;gap:14px">
    <svg width="18" height="15" viewBox="0 0 18 15"><path d="M6 3V1h6v2" fill="none" stroke="#666" stroke-width="1.5"/><rect x="0" y="3" width="18" height="12" rx="1.5" fill="#666"/><path d="M0 8h18" stroke="#fff"/></svg>Business</div>
  <svg class="abs" style="left:1282px;top:20px" width="28" height="28" viewBox="0 0 28 28" fill="none" stroke="#fff" stroke-width="1.8"><circle cx="14" cy="14" r="4.5"/><path d="M14 2v4M14 22v4M2 14h4M22 14h4M5.5 5.5l2.8 2.8M19.7 19.7l2.8 2.8M5.5 22.5l2.8-2.8M19.7 8.3l2.8-2.8"/><circle cx="14" cy="14" r="8.5"/></svg>
  <svg class="abs" style="left:1326px;top:23px" width="20" height="24" viewBox="0 0 20 24"><path d="M10 1 1 5v6c0 6 4 10 9 12 5-2 9-6 9-12V5z" fill="#fff"/><path d="M5 12l4 4 6-7" fill="none" stroke="#9a9da2" stroke-width="2"/></svg>
  <div class="avatar" role="img" aria-label="User avatar photo"></div>
  <div class="userbox" style="left:1408px;top:24px">Owen</div>
  <svg class="abs" style="left:1450px;top:27px" width="16" height="10" viewBox="0 0 16 10" fill="none" stroke="#fff" stroke-width="2"><path d="M1 1l7 7 7-7"/></svg>

  <div class="step done" style="left:392px;width:216px">Review 1<span class="bar-done"></span></div>
  <div class="step current" style="left:624px;width:215px">Review 2<span class="bar-now"></span></div>
  <div class="step todo" style="left:853px;width:98px">Review 3</div>
  <div class="step todo" style="left:969px;width:98px">Review 4</div>

  <p class="copy" style="left:397px;top:290px">The word "grab" is most commonly used as a verb, meaning to take something quickly or suddenly. Imagine you're running late for school. You don't have time for<br>breakfast, so you quickly grab an apple from the kitchen and rush out the door. As you reach the bus stop, your friend waves and says, "Hey! Let's grab a coffee after class."<br>Later, when you sit down, your phone starts ringing. You grab it from your bag and answer.</p>

  <div class="chart-card">
    <svg width="1076" height="505" viewBox="0 0 1076 505" font-family="Lato, sans-serif">
      <g font-size="13" fill="#222">
        <text x="16" y="152">Long-Term Memory</text>
        <text x="16" y="257">Working Memory</text>
        <text x="16" y="328">Short - Term  Memory</text>
        <text x="16" y="372">Forgotten Memory</text>
      </g>
      <rect x="163" y="290" width="61" height="21" fill="#e3e4e6"/><text x="193" y="305" font-size="12" text-anchor="middle">May 18</text>
      <rect x="253" y="122" width="61" height="21" fill="#e3e4e6"/><text x="283" y="137" font-size="12" text-anchor="middle">May 19</text>
      <rect x="180" y="321" width="27" height="89" fill="var(--blue)"/>
      <rect x="321" y="128" width="27" height="282" fill="var(--blue)"/>
      <path d="M207 323C255 328 285 350 319 410" fill="none" stroke="#666" stroke-width="1.4" stroke-dasharray="1.5 3"/>
      <path d="M350 132C460 170 560 210 606 410" fill="none" stroke="#555" stroke-width="2.4" stroke-dasharray="2 6"/>
      <line x1="61" y1="410" x2="1063" y2="410" stroke="#b8babd" stroke-width="2"/>
      <g stroke="#b8babd" stroke-width="1.2">
        <path d="M83 412v15M149 412v15M224 412v15M289 412v15M349 412v15M414 412v15M481 412v15M547 412v15M606 412v15M672 412v15M731 412v15M796 412v15M855 412v15M921 412v15M982 412v15M1048 412v15"/>
      </g>
      <g font-size="13" fill="#555" text-anchor="middle">
        <text x="83" y="445">18 May</text><text x="149" y="445">12.00</text><text x="224" y="445">19 May</text><text x="289" y="445">12.00</text><text x="349" y="445">20 May</text><text x="414" y="445">12.00</text><text x="481" y="445">21 May</text><text x="547" y="445">12.00</text><text x="606" y="445">22 May</text><text x="672" y="445">12.00</text><text x="731" y="445">23 May</text><text x="796" y="445">12.00</text><text x="855" y="445">24 May</text><text x="921" y="445">12.00</text><text x="982" y="445">25 May</text><text x="1048" y="445">12.00</text>
      </g>
      <text x="538" y="475" font-size="14" fill="#222" text-anchor="middle">Data Range</text>
    </svg>
  </div>

  <h2 class="analysis-title">Wordwell Tutor Learning Analysis</h2>
  <p class="copy" style="left:398px;top:1003px">Lorem ipsum dolor sit amet, consectetur adipiscing elit, sed do eiusmod tempor incididunt ut labore et dolore magna aliqua. Ut enim ad minim veniam, quis nostrud<br>exercitation ullamco laboris nisi ut aliquip ex ea commodo consequat. Duis aute irure dolor in reprehenderit in voluptate velit esse cillum dolore eu fugiat nulla pariatur.<br>Excepteur sint occaecat cupidatat non proident, sunt in culpa qui officia deserunt mollit anim id est laborum.</p>
  <footer class="footer">Copyright © 2025  QuillVane</footer>

  <div class="dim"></div>
  <div class="filter-bar lifted" style="color:#fff">All<svg width="18" height="10" viewBox="0 0 18 10"><path d="M0 0h18L9 10z" fill="#fff"/></svg></div>
  <div class="pointer"></div>

  <div class="modal">
    <div class="select">All<svg width="12" height="8" viewBox="0 0 12 8"><path d="M0 0h12L6 8z" fill="#555"/></svg></div>
    <svg class="close" width="20" height="20" viewBox="0 0 20 20" stroke="var(--close)" stroke-width="2.6"><path d="M2 2l16 16M18 2 2 18"/></svg>

    <svg class="mico" style="top:103px" width="28" height="28" viewBox="0 0 28 28" fill="none" stroke="#999" stroke-width="1.6"><path d="M24 14A10 10 0 1 1 14 4"/><path d="M18 5l2 1.2M22 8l1 2" stroke-dasharray="2 2"/><path d="M14 8v6l-3 3"/></svg>
    <span class="mhead" style="top:105px">Short - Term Memory</span>
    <span class="mword current" style="left:95px;top:133px">Grab</span>

    <svg class="mico" style="top:172px" width="30" height="30" viewBox="0 0 30 30" fill="none" stroke="#999" stroke-width="1.6"><circle cx="15" cy="15" r="12"/><circle cx="15" cy="15" r="6" fill="#999"/><circle cx="15" cy="15" r="2.5" fill="#fff" stroke="none"/></svg>
    <span class="mhead" style="top:177px">Working Memory</span>
    <span class="mword" style="left:95px;top:208px">Cool Down</span>
    <span class="mword" style="left:182px;top:208px">Crave</span>
    <span class="mword" style="left:240px;top:208px">Go For</span>
    <span class="mword" style="left:303px;top:208px">Go -To</span>
    <span class="mword" style="left:364px;top:208px">In The Mood For</span>
    <span class="mword" style="left:481px;top:208px">Sip</span>
    <span class="mword" style="left:524px;top:208px">Soothing</span>
    <span class="mword" style="left:601px;top:208px">Stick With</span>
    <span class="mword" style="left:687px;top:208px">Throw In / Throw On</span>

    <svg class="mico" style="top:252px;left:52px" width="18" height="22" viewBox="0 0 22 26"><path d="M5 11V7a6 6 0 0 1 12 0v4" fill="none" stroke="#999" stroke-width="2.4"/><rect x="2" y="11" width="18" height="14" rx="2" fill="#999"/></svg>
    <span class="mhead" style="top:255px">Long-Terms Memory</span>
    <span class="mword" style="left:95px;top:286px">Give It A Try</span>
  </div>
</section>

</div>
</body>
</html>
```